Veranix - Solution provider in business consulting

Veranix is a swiss based company providing solutions for developing markets. The business covers various fields of business consulting, such as supply chain, product costs, quality management and manufacturing management. The Business operates in a efficient, straight and solution oriented manner.
The final design should communicate these characteristics. Asian people as well as as western people shall identify the qualities of the company at first sight.
The customer needs business cards with a simple view but an recognizable design, printed in high quality. Engraved elements such as the globe or simple words are possible.
Available colors are: (RAL)
102/102/102
51/102/102
153/204/153
255/102/51
Font: Calibri

```html
<!DOCTYPE html>
<html lang="en">
<head>
<meta charset="utf-8">
<title>Veranix Business Card</title>
<link rel="stylesheet" href="https://fonts.googleapis.com/css2?family=Carlito:wght@400;700&display=swap">
<style>
  :root {
    --stage: #000000;
    --card-front: #ffffff;
    --card-back: #666666;
    --ink: #555555;
    --ink-dark: #222222;
    --logo-ink: #5e5e5e;
    --reverse-ink: #ffffff;
  }
  * { margin: 0; padding: 0; box-sizing: border-box; }
  html, body {
    width: 1200px; height: 900px; overflow: hidden;
    background: var(--stage);
    font-family: "Carlito", "Calibri", sans-serif;
  }
  .stage { position: relative; width: 1200px; height: 900px; }

  .card { position: absolute; top: 275px; width: 477px; height: 293px; }
  .card--front {
    left: 116px; background: var(--card-front);
    border-radius: 0 52px 0 52px;
  }
  .card--back {
    left: 622px; top: 276px; height: 292px; background: var(--card-back);
    border-radius: 52px 0 52px 0;
  }

  .wordmark {
    position: absolute; left: 30px; top: 70px;
    font-size: 46px; font-weight: 400; letter-spacing: 0.5px;
    color: var(--logo-ink); line-height: 1;
  }
  .wordmark--reverse {
    left: 0; right: 0; top: 116px; text-align: center;
    font-size: 70px; letter-spacing: 1px; color: var(--reverse-ink);
  }

  .holder { position: absolute; right: 20px; top: 35px; text-align: right; line-height: 1.05; }
  .holder__name { font-size: 18px; font-weight: 700; color: var(--ink); }
  .holder__role { font-size: 13px; color: var(--ink-dark); }

  .contacts { position: absolute; right: 20px; top: 140px; list-style: none; }
  .contacts li {
    display: flex; justify-content: flex-end; align-items: center; gap: 7px;
    height: 20px; font-size: 13.5px; color: var(--ink-dark);
  }
  .contacts svg { width: 11px; height: 11px; fill: var(--ink); }

  .address {
    position: absolute; right: 22px; top: 231px; text-align: right;
    font-size: 13.5px; line-height: 18px; color: var(--ink-dark); font-style: normal;
  }
</style>
</head>
<body>
<main class="stage">
  <section class="card card--front">
    <div class="wordmark">veranix</div>

    <div class="holder">
      <div class="holder__name">Marco Lenz</div>
      <div class="holder__role">CEO</div>
    </div>

    <ul class="contacts">
      <li>+41 79 382 5071
        <svg viewBox="0 0 12 12" aria-hidden="true"><path d="M3 0h6a1 1 0 0 1 1 1v10a1 1 0 0 1-1 1H3a1 1 0 0 1-1-1V1a1 1 0 0 1 1-1zm0 1.5v8h6v-8z"/></svg>
      </li>
      <li>+41 71 864 3392
        <svg viewBox="0 0 12 12" aria-hidden="true"><path d="M2.5 0.5l2 2.5-1.2 1.3c.7 1.6 2 2.9 3.4 3.6l1.3-1.2 2.5 2-1.3 2.2C5 10.5 1.3 6.9.5 2z"/></svg>
      </li>
      <li>marco.lenz@veranix.ch
        <svg viewBox="0 0 12 12" aria-hidden="true"><path d="M0 2h12v8H0zm1 1v.4l5 3.2 5-3.2V3z"/></svg>
      </li>
      <li>www.veranix.ch
        <svg viewBox="0 0 12 12" aria-hidden="true"><circle cx="6" cy="6" r="6"/></svg>
      </li>
    </ul>

    <address class="address">
      Veranix GmbH Feldweg 14<br>
      9246 Niederau Switzerland
    </address>
  </section>

  <section class="card card--back">
    <div class="wordmark wordmark--reverse">veranix</div>
  </section>
</main>
</body>
</html>
```